Internal web page of multinational company - Portfolio of reports

We need to improve the look & feel of an existing internal HTML page.
We use it as a portfolios where users go and see a list of existing reports as "tiles". The HTML page is automatically generated by a javascript that reads the contents to display from an HTML file.
What is needs is a "face lift" in the design of the page.
Currently we use icons on the top right of each tile to denote the type of technology used on the report and also colons for the same purpose. The attached screenshots will be self explanatory.
Across the top we have "tabs" that, once selected change the tiles.
Need a proposal for new design that keeps is as clean as possible, specially the home page that should be very light (Plimbo like).
The idea for this page is to serve as a "one stop shop" and become a bookmark for everyone in the company.
Looking for a wow effect that make is visually

Target Market(s)

Internal employees

Industry/Entity Type

It Company

Coding

Coded - Design and coding required

Number of Pages Required

2 page

Requirements
Must have
• Should not change the logo or its position from the bottom left.
• Page must be as clean as possible and
Nice to have
• Welcome to change the logo on the top left. This page is from the CSU M&I (Mni) which stands for Central Support Unit - Metrics & Insight.
Should not have
• Do no use red, this is the color of our competitor. The blue on the bottom is standard for our logo

```html
<!DOCTYPE html>
<html lang="en">
<head>
<meta charset="utf-8">
<title>CSU M&amp;I – Report Portfolio</title>
<link rel="stylesheet" href="https://fonts.googleapis.com/css2?family=Open+Sans:wght@400;600&family=Roboto+Condensed:wght@400;700&display=swap">
<style>
  :root {
    --page-bg: #e9ecf1;
    --header-bg: #ffffff;
    --brand-blue: #3a74ab;
    --input-border: #d5dae2;
    --button-bg: #eef1f5;
    --text-muted: #8a8f96;
    --white: #ffffff;
    --tile-hr: #8a66b9;
    --tile-finance: #e28447;
    --tile-ps: #4aac9b;
    --tile-csu: #4f8cc2;
    --tile-distribution: #4ab1d6;
  }
  * { box-sizing: border-box; margin: 0; padding: 0; }
  html, body {
    width: 1200px;
    height: 495px;
    overflow: hidden;
    background: var(--page-bg);
    font-family: "Open Sans", sans-serif;
  }
  .page { position: relative; width: 1200px; height: 495px; }

  /* Header */
  .site-header {
    position: absolute; left: 0; top: 0; width: 1200px; height: 51px;
    background: var(--header-bg);
    box-shadow: 0 1px 3px rgba(0,0,0,0.08);
  }
  .brand {
    position: absolute; left: 99px; top: 12px;
    display: flex; align-items: center; gap: 8px;
  }
  .brand-dot {
    width: 24px; height: 24px; border-radius: 50%;
    background: var(--brand-blue);
  }
  .brand-name {
    font-family: "Roboto Condensed", sans-serif;
    font-weight: 400; font-size: 23px; line-height: 27px;
    color: var(--brand-blue);
  }
  .search {
    position: absolute; top: 12px; left: 867px;
    display: flex; gap: 3px;
  }
  .search-input {
    width: 172px; height: 30px;
    border: 1px solid var(--input-border); border-radius: 2px;
    font-family: "Open Sans", sans-serif; font-size: 11px;
    color: var(--text-muted); padding: 0 12px; line-height: 28px;
  }
  .search-button {
    width: 29px; height: 30px;
    background: var(--button-bg); border: 1px solid var(--input-border);
    display: flex; align-items: center; justify-content: center;
  }
  .search-button + .search-button { margin-left: -3px; }

  /* Tiles */
  .tile {
    position: absolute; width: 243px; height: 60px;
    display: flex; align-items: center; padding-left: 17px;
    color: var(--white);
    font-family: "Roboto Condensed", sans-serif;
    font-weight: 700; font-size: 18px; letter-spacing: 0.2px;
  }
  .tile-icon {
    width: 40px; height: 40px; border-radius: 50%;
    border: 2px solid var(--white);
    display: flex; align-items: center; justify-content: center;
    margin-right: 14px; flex-shrink: 0;
  }
  .tile-hr { left: 346px; top: 105px; background: var(--tile-hr); }
  .tile-finance { left: 612px; top: 105px; background: var(--tile-finance); }
  .tile-ps { left: 346px; top: 191px; background: var(--tile-ps); }
  .tile-csu { left: 612px; top: 191px; background: var(--tile-csu); }
  .tile-distribution { left: 346px; top: 277px; background: var(--tile-distribution); }

  /* Footer */
  .site-footer {
    position: absolute; left: 0; top: 449px; width: 1200px; height: 46px;
    background: var(--brand-blue); color: var(--white);
  }
  .feedback-button {
    position: absolute; left: 99px; top: 7px; width: 139px; height: 31px;
    border: 1px solid var(--white);
    display: flex; align-items: center; justify-content: center; gap: 8px;
    font-family: "Roboto Condensed", sans-serif; font-weight: 400; font-size: 12px;
  }
  .copyright {
    position: absolute; left: 255px; top: 16px;
    font-size: 8.5px; letter-spacing: 0.1px;
  }
  .footer-brand {
    position: absolute; left: 1014px; top: 12px;
    display: flex; align-items: center; gap: 6px;
  }
  .footer-brand .brand-dot { width: 16px; height: 16px; background: var(--white); }
  .footer-brand .brand-name { font-size: 17px; line-height: 20px; color: var(--white); }
  .build-code {
    position: absolute; left: 1166px; top: 15px;
    font-size: 11px;
  }
</style>
</head>
<body>
<div class="page">
  <header class="site-header">
    <div class="brand">
      <span class="brand-dot"></span>
      <span class="brand-name">CSU M&amp;I</span>
    </div>
    <div class="search">
      <div class="search-input">Search..</div>
      <div class="search-button">
        <svg width="12" height="12" viewBox="0 0 12 12"><circle cx="5" cy="5" r="3.6" fill="none" stroke="#3a74ab" stroke-width="1.8"/><line x1="7.7" y1="7.7" x2="10.8" y2="10.8" stroke="#3a74ab" stroke-width="2" stroke-linecap="round"/></svg>
      </div>
      <div class="search-button">
        <svg width="10" height="10" viewBox="0 0 10 10"><path d="M2 2 L8 8 M8 2 L2 8" stroke="#3a74ab" stroke-width="2" stroke-linecap="round"/></svg>
      </div>
    </div>
  </header>

  <main>
    <a class="tile tile-hr">
      <span class="tile-icon">
        <svg width="18" height="18" viewBox="0 0 18 18"><circle cx="9" cy="5.5" r="3.5" fill="#fff"/><path d="M2.5 16 C2.5 11 5 9.5 9 9.5 C13 9.5 15.5 11 15.5 16 Z" fill="#fff"/></svg>
      </span>HR
    </a>
    <a class="tile tile-finance">
      <span class="tile-icon">
        <svg width="22" height="16" viewBox="0 0 22 16"><rect x="1" y="2" width="20" height="12" fill="none" stroke="#fff" stroke-width="1.8"/><circle cx="11" cy="8" r="3.4" fill="#fff"/><rect x="3.5" y="4.5" width="2" height="7" fill="#fff"/><rect x="16.5" y="4.5" width="2" height="7" fill="#fff"/></svg>
      </span>FINANCE
    </a>
    <a class="tile tile-ps">
      <span class="tile-icon">
        <svg width="20" height="20" viewBox="0 0 20 20"><path d="M18 2 L2 9 L7 11 L15 5 L9 12.5 L9 18 L12 14 L15.5 16 Z" fill="#fff"/></svg>
      </span>P&amp;S
    </a>
    <a class="tile tile-csu">
      <span class="tile-icon">
        <svg width="20" height="20" viewBox="0 0 20 20"><circle cx="10" cy="10" r="8" fill="#fff"/><path d="M6 5 C8 6 8 8 7 9 C6 10 7 12 8.5 12.5 C9 14 8 15.5 8.5 17 M12 4 C11 6 13 7 14.5 7 C15 9 13.5 10 14 12" fill="none" stroke="#4f8cc2" stroke-width="1.6" stroke-linecap="round"/></svg>
      </span>CSU
    </a>
    <a class="tile tile-distribution">
      <span class="tile-icon">
        <svg width="22" height="20" viewBox="0 0 22 20"><path d="M8 3 L2 9 L8 15" fill="none" stroke="#fff" stroke-width="2" stroke-linejoin="round"/><path d="M13 3 L7 9 L13 15 L13 11.5 C17 11.5 19 13.5 20 17.5 C20 11 17 7 13 6.5 Z" fill="#fff"/></svg>
      </span>DISTRIBUTION
    </a>
  </main>

  <footer class="site-footer">
    <div class="feedback-button">
      <svg width="17" height="13" viewBox="0 0 17 13"><ellipse cx="7" cy="5" rx="6" ry="4" fill="none" stroke="#fff" stroke-width="1.4"/><path d="M3 8 L2 11 L6 9" fill="#fff"/><path d="M13.5 3.5 C15.5 4.5 16.5 6 15.5 8 L16 11 L13 9.5 C11.5 10 10 9.8 9 9.3" fill="none" stroke="#fff" stroke-width="1.4"/></svg>
      HELP &amp; FEEDBACK
    </div>
    <p class="copyright">COPYRIGHTS 2015. CSU M&amp;I. ALL RIGHTS RESERVED.</p>
    <div class="footer-brand">
      <span class="brand-dot"></span>
      <span class="brand-name">CSU M&amp;I</span>
    </div>
    <span class="build-code">C8</span>
  </footer>
</div>
</body>
</html>
```